Create a business promotion flyer to leave in customer mailboxes. We are a bulk petroleum supplier, servicing any industry that requires diesel. Base in griffith NSW, servicing griffith area and surrounds.

Business Name - Terra Diesel
Fuel@terradiesel-example.com.au
Owen - 0491 570 362 ohartley@terradiesel-example.com.au
Liam - 0491 570 718 lprosser@terradiesel-example.com.au
Simon - 0491 570 905 skenway@terradiesel-example.com.au
Office 02 5550 1734

Bulk Fuel deliveries.
Oils & lubricants
Local Family owned business

```html
<!DOCTYPE html>
<html lang="en">
<head>
<meta charset="utf-8">
<title>Terra Diesel – Bulk Fuel Flyer</title>
<link href="https://fonts.googleapis.com/css2?family=Outfit:wght@400;500;600;700;800&family=Poppins:wght@400;500&display=swap" rel="stylesheet">
<style>
  :root{
    --red:#ee2a1e;
    --ink:#141414;
    --paper:#efefee;
    --dark:#2a2a2a;
    --white:#ffffff;
  }
  html,body{margin:0;padding:0;overflow:hidden;}
  body{background:#ddd;}
  .flyer{position:relative;width:927px;height:1200px;overflow:hidden;background:var(--paper);font-family:'Outfit',sans-serif;color:var(--ink);}
  .hero-photo{position:absolute;left:0;top:0;width:927px;height:560px;
    background:linear-gradient(180deg,#b9d0e6 0%,#dfe9f2 30%,#c9cccf 48%,#8e949a 62%,#e6e6e6 88%,var(--paper) 100%);}
  .brand{position:absolute;top:95px;left:0;width:927px;text-align:center;font-weight:700;font-size:64px;color:var(--red);letter-spacing:1px;display:flex;justify-content:center;align-items:center;gap:16px;}
  .brand-dot{width:30px;height:30px;border-radius:50%;background:var(--red);}
  .feature{position:absolute;top:502px;text-align:center;}
  .feature-icon{width:50px;height:50px;border-radius:50%;background:var(--red);margin:0 auto;display:flex;align-items:center;justify-content:center;}
  .feature-label{position:absolute;top:562px;font-size:19px;font-weight:600;white-space:nowrap;transform:translateX(-50%);}
  .headline{position:absolute;top:592px;left:0;width:927px;text-align:center;font-size:43px;font-weight:800;color:var(--red);margin:0;letter-spacing:.3px;}
  .intro{position:absolute;left:54px;top:661px;width:418px;font-size:15.5px;line-height:27px;text-align:justify;margin:0;letter-spacing:.4px;}
  .banner{position:absolute;left:0;top:757px;width:471px;height:45px;}
  .banner-title{position:absolute;left:54px;top:759px;font-size:24px;font-weight:600;color:var(--white);margin:0;line-height:40px;}
  .lead{position:absolute;left:55px;top:815px;width:420px;font-size:16.5px;font-weight:500;line-height:27px;margin:0;}
  .sectors{position:absolute;left:81px;top:883px;margin:0;padding:0;list-style:none;}
  .sector{display:flex;align-items:center;height:42px;margin-bottom:17.5px;}
  .sector-icon{width:42px;height:42px;border-radius:50%;background:radial-gradient(circle at 40% 35%,#4a4a4a,#161616);display:flex;align-items:center;justify-content:center;box-shadow:0 2px 4px rgba(0,0,0,.3);}
  .sector-name{margin-left:19px;font-size:17.5px;font-weight:500;letter-spacing:.3px;}
  .swoosh{position:absolute;left:0;top:0;}
  .card{position:absolute;left:540px;top:692px;width:330px;height:453px;background:var(--white);border-radius:24px;}
  .card-bump{position:absolute;left:653px;top:657px;width:104px;height:104px;border-radius:50%;background:var(--white);}
  .card-badge{position:absolute;left:664px;top:672px;width:82px;height:82px;border-radius:50%;background:var(--red);display:flex;align-items:center;justify-content:center;}
  .card-title{position:absolute;left:540px;top:764px;width:330px;text-align:center;font-size:23px;font-weight:600;margin:0;}
  .contact{position:absolute;left:540px;width:330px;text-align:center;}
  .contact-name{margin:0 auto;width:118px;height:32px;border-radius:16px;background:var(--red);color:var(--white);font-weight:600;font-size:15px;display:flex;align-items:center;justify-content:center;gap:12px;letter-spacing:.5px;}
  .contact-line{font-family:'Poppins',sans-serif;font-size:12px;color:#333;display:flex;align-items:center;justify-content:center;gap:12px;height:21px;margin-top:5px;}
  .contact-line.phone{margin-top:11px;font-size:12.5px;}
  .footer-call{position:absolute;left:55px;top:1137px;width:50px;height:50px;border-radius:50%;background:var(--white);display:flex;align-items:center;justify-content:center;}
  .office-label{position:absolute;left:128px;top:1134px;font-family:'Poppins',sans-serif;font-size:13px;color:var(--white);}
  .office-number{position:absolute;left:126px;top:1148px;font-size:38px;font-weight:800;color:var(--white);letter-spacing:.5px;}
  .footer-mail{position:absolute;left:426px;top:1166px;}
  .footer-email{position:absolute;left:468px;top:1161px;font-size:17px;font-weight:500;color:var(--white);letter-spacing:.2px;}
</style>
</head>
<body>
<main class="flyer">
  <div class="hero-photo" role="img" aria-label="Photo of a white fuel tanker road train parked in front of a large steel warehouse under a blue cloudy sky"></div>

  <div class="brand"><span class="brand-dot"></span>Terra Diesel</div>

  <div class="feature" style="left:201px">
    <div class="feature-icon">
      <svg width="30" height="30" viewBox="0 0 30 30" fill="none" stroke="#fff" stroke-width="1.6"><rect x="3" y="9" width="15" height="10" rx="4"/><path d="M18 12h5l4 4v3h-9z"/><circle cx="8" cy="21" r="2.3"/><circle cx="22" cy="21" r="2.3"/></svg>
    </div>
  </div>
  <div class="feature" style="left:383px">
    <div class="feature-icon">
      <svg width="30" height="30" viewBox="0 0 30 30" fill="none" stroke="#fff" stroke-width="1.6"><path d="M10 4c-3 5-5 7-5 10a5 5 0 0 0 10 0c0-3-2-5-5-10z"/><path d="M19 10c-3 5-6 8-6 11a6 6 0 0 0 12 0c0-3-3-6-6-11z"/></svg>
    </div>
  </div>
  <div class="feature" style="left:612px">
    <div class="feature-icon">
      <svg width="30" height="30" viewBox="0 0 30 30" fill="none" stroke="#fff" stroke-width="1.6"><circle cx="9" cy="7" r="2.5"/><circle cx="20" cy="7" r="2.5"/><circle cx="15" cy="15" r="2"/><path d="M5 14l4-3 4 3M16 11l4 0 5-3M9 11v15M20 11v15M13 26v-7h4v7"/></svg>
    </div>
  </div>
  <div class="feature-label" style="left:224px">Bulk Fuel deliveries</div>
  <div class="feature-label" style="left:414px">Oils &amp; lubricants</div>
  <div class="feature-label" style="left:655px">Local Family-owned business</div>

  <h1 class="headline">KEEPING YOUR BUSINESS MOVING</h1>

  <p class="intro">Based in Griffith, NSW, we're committed to providing reliable service, competitive pricing, and personalised support to local businesses.</p>

  <svg class="banner" viewBox="0 0 471 45"><polygon points="0,0 471,0 449,45 0,45" fill="var(--red)"/></svg>
  <h2 class="banner-title">Local Family-Owned Business</h2>

  <p class="lead">Terra Diesel delivers quality bulk diesel directly to your site when you need it.</p>

  <ul class="sectors">
    <li class="sector"><span class="sector-icon"><svg width="24" height="24" viewBox="0 0 24 24" fill="none" stroke="#fff" stroke-width="1.3"><circle cx="7" cy="16" r="4"/><circle cx="18" cy="17" r="3"/><path d="M5 11V6h7l2 5h6v4M12 6v5"/></svg></span><span class="sector-name">Agriculture &amp; Farming</span></li>
    <li class="sector"><span class="sector-icon"><svg width="24" height="24" viewBox="0 0 24 24" fill="none" stroke="#fff" stroke-width="1.3"><rect x="5" y="3" width="14" height="16" rx="2"/><path d="M5 11h14M8 15h1M15 15h1M7 19v2M17 19v2"/></svg></span><span class="sector-name">Transport &amp; Logistics</span></li>
    <li class="sector"><span class="sector-icon"><svg width="24" height="24" viewBox="0 0 24 24" fill="none" stroke="#fff" stroke-width="1.3"><path d="M2 16V8l11 2v6zM13 11h5l4 3v2h-9"/><circle cx="6" cy="18" r="2"/><circle cx="18" cy="18" r="2"/></svg></span><span class="sector-name">Construction &amp; Earthmoving</span></li>
    <li class="sector"><span class="sector-icon"><svg width="24" height="24" viewBox="0 0 24 24" fill="none" stroke="#fff" stroke-width="1.3"><path d="M3 21V11l5 3v-3l5 3v-3l5 3V5h3v16z"/><path d="M6 17h2M11 17h2M16 17h2"/></svg></span><span class="sector-name">Industrial Operations</span></li>
  </ul>

  <svg class="swoosh" width="927" height="1200" viewBox="0 0 927 1200"><path d="M0 1124 C300 1118 560 1070 720 1010 C800 975 870 935 927 885 V1200 H0 Z" fill="var(--red)"/></svg>

  <div class="card"></div>
  <div class="card-bump"></div>
  <div class="card-badge">
    <svg width="50" height="50" viewBox="0 0 50 50" fill="none" stroke="#fff" stroke-width="2"><circle cx="25" cy="17" r="5"/><path d="M16 31c1-6 5-8 9-8s8 2 9 8z"/><path d="M11 21a15 15 0 0 1 26-9M39 18a15 15 0 0 1-2 12"/><path d="M6 38l7-4h9l8-3 5 2-12 9H10"/></svg>
  </div>
  <h2 class="card-title">Contact Our Team</h2>

  <div class="contact" style="top:810px">
    <div class="contact-name"><svg width="13" height="13" viewBox="0 0 14 14" fill="#fff"><circle cx="7" cy="4" r="3.3"/><path d="M1 14c0-4 3-6 6-6s6 2 6 6z"/></svg>OWEN</div>
    <div class="contact-line phone"><svg width="12" height="12" viewBox="0 0 12 12"><rect width="12" height="12" rx="2" fill="#222"/><path d="M3.5 3l1.5 0 .7 1.7-1 .8a5 5 0 0 0 1.8 1.8l.8-1 1.7.7V8.5A1 1 0 0 1 8 9.3 6 6 0 0 1 2.7 4 1 1 0 0 1 3.5 3z" fill="#fff"/></svg>0491 570 362</div>
    <div class="contact-line"><svg width="14" height="11" viewBox="0 0 14 11"><rect width="14" height="11" rx="1" fill="#222"/><path d="M1 1.5l6 4.5 6-4.5" stroke="#fff" fill="none"/></svg>ohartley@terradiesel-example.com.au</div>
  </div>
  <div class="contact" style="top:920px">
    <div class="contact-name"><svg width="13" height="13" viewBox="0 0 14 14" fill="#fff"><circle cx="7" cy="4" r="3.3"/><path d="M1 14c0-4 3-6 6-6s6 2 6 6z"/></svg>LIAM</div>
    <div class="contact-line phone"><svg width="12" height="12" viewBox="0 0 12 12"><rect width="12" height="12" rx="2" fill="#222"/><path d="M3.5 3l1.5 0 .7 1.7-1 .8a5 5 0 0 0 1.8 1.8l.8-1 1.7.7V8.5A1 1 0 0 1 8 9.3 6 6 0 0 1 2.7 4 1 1 0 0 1 3.5 3z" fill="#fff"/></svg>0491 570 718</div>
    <div class="contact-line"><svg width="14" height="11" viewBox="0 0 14 11"><rect width="14" height="11" rx="1" fill="#222"/><path d="M1 1.5l6 4.5 6-4.5" stroke="#fff" fill="none"/></svg>lprosser@terradiesel-example.com.au</div>
  </div>
  <div class="contact" style="top:1029px">
    <div class="contact-name"><svg width="13" height="13" viewBox="0 0 14 14" fill="#fff"><circle cx="7" cy="4" r="3.3"/><path d="M1 14c0-4 3-6 6-6s6 2 6 6z"/></svg>SIMON</div>
    <div class="contact-line phone"><svg width="12" height="12" viewBox="0 0 12 12"><rect width="12" height="12" rx="2" fill="#222"/><path d="M3.5 3l1.5 0 .7 1.7-1 .8a5 5 0 0 0 1.8 1.8l.8-1 1.7.7V8.5A1 1 0 0 1 8 9.3 6 6 0 0 1 2.7 4 1 1 0 0 1 3.5 3z" fill="#fff"/></svg>0491 570 905</div>
    <div class="contact-line"><svg width="14" height="11" viewBox="0 0 14 11"><rect width="14" height="11" rx="1" fill="#222"/><path d="M1 1.5l6 4.5 6-4.5" stroke="#fff" fill="none"/></svg>skenway@terradiesel-example.com.au</div>
  </div>

  <div class="footer-call">
    <svg width="28" height="28" viewBox="0 0 28 28" fill="none" stroke="var(--red)" stroke-width="1.6"><path d="M5 8l3-2 3 5-2 2a10 10 0 0 0 5 5l2-2 5 3-2 3C11 22 6 16 5 8z"/><path d="M14 4h9a2 2 0 0 1 2 2v5a2 2 0 0 1-2 2h-4l-3 3v-3h-2a2 2 0 0 1-2-2V6a2 2 0 0 1 2-2z"/></svg>
  </div>
  <div class="office-label">Office</div>
  <div class="office-number">02 5550 1734</div>
  <svg class="footer-mail" width="22" height="16" viewBox="0 0 22 16"><rect width="22" height="16" rx="2" fill="#fff"/><path d="M2 2l9 7 9-7" stroke="var(--red)" stroke-width="1.8" fill="none"/></svg>
  <div class="footer-email">Email Us: Fuel@terradiesel-example.com.au</div>
</main>
</body>
</html>
```